Health Supplement Series for 60 tablets of pure Amber Vine Core powder

We need a packaging design theme for a health supplement for international consumers. Our initial product is called 'Amber Vine Core'. It is for general health and is particularly effective for diabetic symptoms.
We would like to see designs that are clean and fresh.
It should give the impression of professional, premium pharmaceutical grade products.
Our company logo is attached below.

Target Market(s)

International

Industry/Entity Type

Health And Wellness

Font styles to use
Serif
Sans Serif

Requirements
Must have
• Bottle and box packaging required.
• 1st product is bottle of 60 tablets of 0.5gm each.
Should not have
• Seals and other "must buy" "guaranteed" etc

```html
<!DOCTYPE html>
<html lang="en">
<head>
<meta charset="utf-8">
<title>Amber Vine Core – Label</title>
<link rel="stylesheet" href="https://fonts.googleapis.com/css2?family=Oswald:wght@400;500&family=Raleway:wght@600&display=swap">
<style>
  :root {
    --canvas: #ececec;
    --label-white: #ffffff;
    --brand-green: #5aa83a;
    --band-green: #62ad45;
    --band-green-light: #78bc5a;
    --text-white: #ffffff;
    --seed-light: #e9b072;
    --seed-dark: #b5763a;
  }
  * { margin: 0; padding: 0; box-sizing: border-box; }
  html, body {
    width: 1200px;
    height: 1200px;
    overflow: hidden;
    background: var(--canvas);
  }
  .canvas {
    position: relative;
    width: 1200px;
    height: 1200px;
    display: flex;
    align-items: center;
    justify-content: center;
  }
  .label {
    position: relative;
    width: 820px;
    height: 900px;
    background: var(--label-white);
    border-top: 8px solid var(--brand-green);
    border-bottom: 8px solid var(--brand-green);
    box-shadow: 0 10px 40px rgba(0,0,0,0.08);
  }
  .brand {
    position: absolute;
    top: 170px;
    left: 0;
    right: 0;
    display: flex;
    justify-content: center;
    align-items: center;
    gap: 18px;
  }
  .brand-square {
    width: 104px;
    height: 128px;
    background: var(--brand-green);
  }
  .brand-name {
    font-family: "Raleway", sans-serif;
    font-weight: 600;
    color: var(--brand-green);
    line-height: 1;
  }
  .brand-name .main {
    display: block;
    font-size: 84px;
    letter-spacing: 10px;
  }
  .brand-name .sub {
    display: block;
    margin-top: 10px;
    font-size: 35px;
    letter-spacing: 1px;
  }
  .product-band {
    position: absolute;
    left: 0;
    right: 0;
    top: 426px;
    bottom: 0;
    background: linear-gradient(135deg, var(--band-green-light) 0%, var(--band-green) 55%);
  }
  .product-name {
    position: absolute;
    top: 24px;
    left: 0;
    right: 0;
    text-align: center;
    font-family: "Oswald", sans-serif;
    font-weight: 500;
    font-size: 94px;
    letter-spacing: -1px;
    color: var(--text-white);
    text-transform: uppercase;
  }
  .product-photo {
    position: absolute;
    left: 320px;
    top: 200px;
    width: 350px;
    height: 240px;
    border-radius: 40% 50% 45% 40%;
    background: radial-gradient(ellipse at 55% 40%, var(--seed-light) 0%, var(--seed-dark) 80%, rgba(181,118,58,0) 100%);
  }
  .product-count {
    position: absolute;
    left: 80px;
    top: 340px;
    font-family: "Oswald", sans-serif;
    color: var(--text-white);
    line-height: 1.1;
  }
  .product-count .tablets {
    display: block;
    font-size: 38px;
    font-weight: 400;
  }
  .product-count .weight {
    display: block;
    font-family: "Raleway", sans-serif;
    font-size: 26px;
    font-weight: 600;
  }
</style>
</head>
<body>
  <main class="canvas">
    <section class="label">
      <header class="brand">
        <span class="brand-square" aria-hidden="true"></span>
        <span class="brand-name">
          <span class="main">LUMORA</span>
          <span class="sub">BIOTECH LIMITED</span>
        </span>
      </header>
      <div class="product-band">
        <h1 class="product-name">Amber Vine Core</h1>
        <div class="product-photo" role="img" aria-label="Photo of dried golden-brown seed pods"></div>
        <p class="product-count">
          <span class="tablets">60 TABLETS</span>
          <span class="weight">0.5gm each</span>
        </p>
      </div>
    </section>
  </main>
</body>
</html>
```